tinyTally Resource Book - 10 maths tasks to do outside

I need a 22 (11 pages back to back) page A6 sized book produced to standard for submission to professional printer. Needs to be as .pdf file showing guide lines and allowances for colour bleed. I have text already written and submitted as attachment in a Word file with margins set to A6 size. The theme of the materials is "Nature Play" so using lots of pictures from nature (Australia preferably) and showing lots of patterns in nature (rocks, leaves, flower petals etc). Some of the tasks refer to specific activities, such as "shadows" and "floating" so would be great to illustrate appropriately. The big emphasis is on learning outside the classroom, getting kids to engage actively with nature. I would like to see the pages as full colour - so not white background. The book itself will be spiral bound along the top edge so a margin of at least 1cm will be required at the top of each page (or the bottom of even numbered pages). Book will be printed on plastic laminated matte paper for outdoor use. Font size needs to be big enough to read. Fonts sizes, alignments and page numbers are all different at the moment and need to be standardised. One photo is included in a page as a sample if you can use it, otherwise disregard. Logo for Wattlebrook Numeracy Guild is also included to have as part of the acknowledgements at the back of the book.

Target Market(s)

Book is for early childhood and preschool teachers.

Industry/Entity Type

Education

Font styles to use
Sans Serif

Requirements
Must have
• Colour and appeal.
Nice to have
• Use of natural colours instead of bright catchy colours but that is your call.
Should not have
• American spelling

```html
<!DOCTYPE html>
<html lang="en-AU">
<head>
<meta charset="utf-8">
<title>4. One More – tinyTally Resource Book</title>
<link rel="stylesheet" href="https://fonts.googleapis.com/css2?family=Jost:ital,wght@0,400;0,500;0,700;0,800;1,700;1,800&display=swap">
<style>
  :root {
    --wood-light: #efc993;
    --wood-mid: #e2b47a;
    --wood-deep: #d29f62;
    --leaf-green: #0c9a3c;
    --ink: #161310;
    --halo: #ffffff;
    --bullet-red: #c8102e;
    --leaf-lime: #c9dc4a;
    --leaf-yellow: #e8ec8a;
  }
  * { margin: 0; padding: 0; box-sizing: border-box; }
  html, body { width: 848px; height: 1200px; overflow: hidden; }
  body { font-family: "Jost", "Century Gothic", sans-serif; color: var(--ink); }

  .page {
    position: relative;
    width: 848px;
    height: 1200px;
    overflow: hidden;
  }
  .wood-texture {
    position: absolute;
    inset: 0;
    background: linear-gradient(100deg, var(--wood-light) 0%, var(--wood-mid) 45%, var(--wood-light) 70%, var(--wood-deep) 100%);
  }
  .leaf-sprig {
    position: absolute;
    border-radius: 50% 40% 50% 45%;
    background: radial-gradient(ellipse at 45% 40%, var(--leaf-yellow) 0%, var(--leaf-lime) 55%, rgba(201,220,74,0) 75%);
  }
  .leaf-sprig--upper { left: 520px; top: 830px; width: 290px; height: 160px; }
  .leaf-sprig--lower { left: 530px; top: 960px; width: 280px; height: 150px; }

  .content { position: relative; }

  .task-title {
    position: absolute;
    top: 32px; left: 0; width: 848px;
    text-align: center;
    font-weight: 800;
    font-size: 58px;
    line-height: 1;
    color: var(--leaf-green);
    text-shadow: 0 0 3px var(--halo), 0 0 3px var(--halo), 0 0 2px var(--halo);
  }
  .outcome {
    position: absolute;
    top: 122px; left: 40px; width: 768px;
    text-align: center;
    font-weight: 800;
    font-size: 36px;
    line-height: 46px;
    color: var(--leaf-green);
    text-shadow: 0 0 3px var(--halo), 0 0 3px var(--halo), 0 0 2px var(--halo);
  }
  .lead {
    position: absolute;
    left: 58px; width: 720px;
    font-style: italic;
    font-weight: 800;
    font-size: 32px;
    line-height: 43px;
    color: var(--leaf-green);
    text-shadow: 0 0 2px var(--halo), 0 0 2px var(--halo);
  }
  .statement {
    position: absolute;
    left: 138px; width: 680px;
    font-weight: 400;
    font-size: 38px;
    line-height: 47px;
    letter-spacing: 0.3px;
  }
  .lead--children { top: 292px; }
  .statement--children { top: 374px; }
  .lead--educators { top: 524px; }
  .statement--educators { top: 609px; }
  .lead--task { top: 762px; }

  .opportunities {
    position: absolute;
    top: 806px; left: 138px; width: 420px;
    list-style: none;
    font-size: 29px;
    line-height: 41px;
  }
  .opportunities li {
    position: relative;
    padding-left: 28px;
    margin-bottom: 3px;
  }
  .opportunities li::before {
    content: "";
    position: absolute;
    left: 2px; top: 13px;
    width: 13px; height: 13px;
    background: var(--bullet-red);
    transform: rotate(45deg);
  }
</style>
</head>
<body>
<main class="page">
  <div class="wood-texture" role="img" aria-label="Light timber board background texture"></div>
  <div class="leaf-sprig leaf-sprig--upper" role="img" aria-label="Sprig of fresh lime-green leaves"></div>
  <div class="leaf-sprig leaf-sprig--lower" role="img" aria-label="Second sprig of fresh lime-green leaves"></div>

  <section class="content">
    <h1 class="task-title">4. One More</h1>
    <h2 class="outcome">EYLF – Outcome 2: Children are connected with and contribute to their world</h2>

    <p class="lead lead--children">Children become aware of fairness when they...</p>
    <p class="statement statement--children">are empowered to make choices and problem solve to meet their needs in particular contexts</p>

    <p class="lead lead--educators">Educators promote this learning when they...</p>
    <p class="statement statement--educators">engage children in discussions about respectful and equal relations</p>

    <p class="lead lead--task">This task provides an opportunity to:</p>
    <ul class="opportunities">
      <li>explore the concepts of “equal” and “more”</li>
      <li>discuss how inequity happens</li>
      <li>explore sharing equally</li>
      <li>develop strategies for dealing with inequity</li>
    </ul>
  </section>
</main>
</body>
</html>
```